Business card for my new company (Accounting firm)

I need a business card for my new business Brightwell Advisory and Ledger SA. Our services are accounting, tax, audit and financial management. Our customers are small companies, start-ups and new companies. The final design has to show financial security, trust and growth. Please find our logo attached to the business card. Text for the business card: Brightwell Advisory and Ledger SA Tomas Varenholt Director and Founder Certified Accountant Tel. 022 418 57 34 tv@clairevalconseil.ch www.clairevalconseil.ch Rue des Vergières 27 1201 Geneva
Target Market(s)
Our customers are small companies, start-ups and new companies.
Industry/Entity Type
Finance And Accounting
Contact Information for Business Card
Claireval Conseil et Comptes SA
Tomas Varenholt
Directeur et Fondateur
Expert-comptable diplômé
Tél. 022 418 57 34
tv@clairevalconseil.ch
www.clairevalconseil.ch
Rue des Vergières 27
1201 Genève

```html
<!DOCTYPE html>
<html lang="fr">
<head>
<meta charset="utf-8">
<title>Claireval Conseil et Comptes SA – Carte de visite</title>
<link rel="stylesheet" href="https://fonts.googleapis.com/css2?family=Roboto:wght@300;400;500;700&display=swap">
<style>
  :root {
    --backdrop: #3a3b3d;
    --card: #1f2023;
    --card-edge: #17181a;
    --blue: #2a9bd8;
    --blue-deep: #1a6fae;
    --blue-light: #3cb4ec;
    --white: #ffffff;
    --text-soft: #e6edf2;
    --emboss: #2b2c30;
  }
  * { box-sizing: border-box; margin: 0; padding: 0; }
  html, body {
    width: 799px; height: 1200px; overflow: hidden;
    background: var(--backdrop);
    font-family: "Roboto", Arial, sans-serif;
  }
  .sheet {
    width: 799px; height: 1200px;
    display: flex; flex-direction: column; align-items: center; justify-content: space-around;
    padding: 60px 0;
  }
  .card {
    position: relative;
    width: 640px; height: 370px;
    background: var(--card);
    overflow: hidden;
    box-shadow: 0 18px 40px rgba(0,0,0,.45);
  }
  /* front */
  .card-front .edge-band {
    position: absolute; left: 0; right: 0; bottom: 0; height: 16px;
    background: linear-gradient(90deg, var(--blue-deep), var(--blue-light));
  }
  .card-front .brand-name {
    position: absolute; left: 0; right: 0; top: 140px;
    text-align: center;
    font-weight: 500; font-size: 34px; line-height: 44px; letter-spacing: 2px;
    color: var(--emboss);
  }
  .brand-mark {
    display: inline-block; width: 20px; height: 20px; border-radius: 50%;
    background: currentColor; vertical-align: middle; margin-right: 12px;
  }
  /* back */
  .card-back .waves { position: absolute; inset: 0; width: 100%; height: 100%; }
  .card-back .brand-name {
    position: absolute; left: 40px; top: 150px; width: 230px;
    font-weight: 500; font-size: 30px; line-height: 38px; letter-spacing: 1px;
    color: var(--white);
  }
  .holder {
    position: absolute; right: 28px; top: 92px; text-align: right; color: var(--white);
  }
  .holder-name { font-weight: 700; font-size: 26px; margin-bottom: 4px; }
  .holder-role { font-weight: 400; font-size: 15px; line-height: 19px; color: var(--text-soft); }
  .contact {
    position: absolute; right: 28px; bottom: 30px; text-align: right;
    color: var(--white); font-size: 17px; line-height: 22px; list-style: none;
  }
  .contact .address { margin-bottom: 10px; padding-right: 26px; }
  .contact li { display: flex; justify-content: flex-end; align-items: center; gap: 10px; }
  .contact svg { width: 16px; height: 16px; fill: var(--blue); flex: none; }
</style>
</head>
<body>
<main class="sheet">
  <section class="card card-front">
    <p class="brand-name"><span class="brand-mark"></span>Claireval<br>Conseil et Comptes SA</p>
    <div class="edge-band"></div>
  </section>

  <section class="card card-back">
    <svg class="waves" viewBox="0 0 640 370" preserveAspectRatio="none" aria-hidden="true">
      <defs>
        <linearGradient id="bandFill" x1="0" y1="0" x2="1" y2="1">
          <stop offset="0" stop-color="#2fa9e4"/>
          <stop offset="1" stop-color="#1766a8"/>
        </linearGradient>
      </defs>
      <path d="M170 0 H640 V212 C560 196 470 160 390 108 C320 62 250 22 170 0 Z" fill="url(#bandFill)"/>
      <path d="M150 12 C250 30 330 80 400 128 C470 176 560 212 640 226" fill="none" stroke="#1f2023" stroke-width="10"/>
      <path d="M120 22 C240 40 330 100 400 146 C470 192 560 226 640 240" fill="none" stroke="#2a9bd8" stroke-width="5"/>
      <path d="M180 4 C260 16 320 40 370 64" fill="none" stroke="#3cb4ec" stroke-width="3"/>
    </svg>

    <p class="brand-name"><span class="brand-mark" style="color:#2a9bd8"></span>Claireval Conseil et Comptes SA</p>

    <div class="holder">
      <p class="holder-name">Tomas Varenholt</p>
      <p class="holder-role">Directeur et Fondateur<br>Expert-comptable diplômé</p>
    </div>

    <ul class="contact">
      <li class="address">Rue des Vergières 27<br>1201 Genève</li>
      <li>022 418 57 34
        <svg viewBox="0 0 24 24"><path d="M6.6 10.8c1.4 2.8 3.8 5.1 6.6 6.6l2.2-2.2c.3-.3.7-.4 1-.2 1.1.4 2.3.6 3.6.6.6 0 1 .4 1 1V20c0 .6-.4 1-1 1C10.6 21 3 13.4 3 4c0-.6.4-1 1-1h3.5c.6 0 1 .4 1 1 0 1.3.2 2.5.6 3.6.1.3 0 .7-.2 1z"/></svg>
      </li>
      <li>tv@clairevalconseil.ch
        <svg viewBox="0 0 24 24"><path d="M2 5h20v14H2z M4 7v.5l8 5 8-5V7l-8 5z" fill-rule="evenodd"/></svg>
      </li>
      <li>www.clairevalconseil.ch
        <svg viewBox="0 0 24 24"><circle cx="12" cy="12" r="10"/><path d="M2 12h20M12 2c3 3 3 17 0 20M12 2c-3 3-3 17 0 20" stroke="#1f2023" stroke-width="1.5" fill="none"/></svg>
      </li>
    </ul>
  </section>
</main>
</body>
</html>
```